Sophisticated, clean website reflecting my feminine, playful side to sell my abstract art,

I need a website no more than 3 pages to showcase my paintings, a little about me and some contact info. I do abstracts so looking for something a little edgy, yet feminine and current.
Updates

Hi there, These are some artists websites that I Iike: Marnelvoss.com (I like how airy it is) peterwallombry.com garethpolvens.com (I like how it scrolls) I'll need a place for a photo ( a headshot-i do not have it yet so I'll need to be able to upload that later) as well as an area for my bio. Also, it's important that I will be able to upload any new photos and descriptions easily so it should be user friendly. Lastly, I like in a sunny place so would like to have this seem upbeat and playful as that is how i like to paint. thanks-I'm trying to upload my photos now -

Target Market(s)

ppl ages 35-70 who want large scale art for their homes

Industry/Entity Type

art

Coding

Coded - Design and coding required

Number of Pages Required

3 page

Colors

Designer to choose colors to be used in the design.

Requirements
Must have
• photos of my art, a place for my bio, be easy to reach me. tasteful-nothing too "in your face" -my clients are pretty high end and organized. They like clean lines
Nice to have
• sophisticated background, muted tones in the back-similar clean font throughout-no cursive
Should not have
• too many dark areas. Too many blocks of color. Too serious.

```html
<!DOCTYPE html>
<html lang="en">
<head>
<meta charset="utf-8">
<title>About Me – Lorna Vessey Art</title>
<link rel="stylesheet" href="https://fonts.googleapis.com/css2?family=Playfair+Display:wght@600&family=Poppins:wght@300;400;500&family=Tinos&display=swap">
<style>
  :root {
    --ink: #111111;
    --nav-muted: #5f5f5f;
    --body-text: #3a3a3a;
    --rule: #c9c9c9;
    --footer-bg: #f8f8f8;
    --page-bg: #ffffff;
    --photo-top: #dfe7e8;
    --photo-mid: #8a6a55;
    --photo-bottom: #1e1c1c;
  }
  * { box-sizing: border-box; margin: 0; padding: 0; }
  html, body { width: 1200px; height: 1003px; overflow: hidden; background: var(--page-bg); }
  body { position: relative; font-family: "Poppins", sans-serif; color: var(--ink); }

  .site-header {
    position: absolute; top: 0; left: 0; width: 1200px; height: 66px;
    border-bottom: 1px solid var(--rule);
    display: flex; align-items: center; justify-content: center;
  }
  .site-title {
    font-family: "Playfair Display", serif; font-weight: 600;
    font-size: 35px; letter-spacing: -0.3px; color: var(--ink);
  }

  .main-nav { position: absolute; top: 84px; left: 0; width: 1200px; height: 26px; }
  .main-nav a {
    position: absolute; transform: translateX(-50%);
    font-size: 17px; font-weight: 400; color: var(--nav-muted);
    text-decoration: none; white-space: nowrap;
  }
  .main-nav a.is-current { color: var(--ink); font-weight: 500; }

  .portrait {
    position: absolute; left: 100px; top: 168px; width: 481px; height: 586px;
    background: linear-gradient(180deg, var(--photo-top) 0%, #c9b3a2 35%, var(--photo-mid) 60%, var(--photo-bottom) 100%);
  }

  .about-copy { position: absolute; left: 606px; top: 152px; width: 500px; }
  .about-title { font-size: 35px; font-weight: 400; line-height: 50px; color: var(--ink); }
  .about-copy p {
    margin-left: 3px; margin-top: 14px;
    font-size: 16.6px; font-weight: 300; line-height: 35px;
    color: var(--body-text); text-align: justify; text-align-last: left;
  }
  .about-copy p + p { margin-top: 16px; }

  .site-footer {
    position: absolute; left: 0; top: 849px; width: 1200px; height: 154px;
    background: var(--footer-bg);
  }
  .social-links { position: absolute; top: 40px; left: 0; width: 1200px; display: flex; justify-content: center; gap: 6px; }
  .social-links a {
    width: 38px; height: 38px; border: 1.3px solid var(--ink); border-radius: 50%;
    display: flex; align-items: center; justify-content: center;
    font-size: 8px; font-weight: 500; color: var(--ink); text-decoration: none;
  }
  .copyright {
    position: absolute; top: 98px; left: 0; width: 1200px; text-align: center;
    font-family: "Tinos", serif; font-size: 16px; color: var(--ink);
  }
</style>
</head>
<body>
  <header class="site-header">
    <h1 class="site-title">Lorna Vessey Art</h1>
  </header>

  <nav class="main-nav">
    <a href="#" style="left:312px">HOME</a>
    <a href="#" class="is-current" style="left:476px">ABOUT ME</a>
    <a href="#" style="left:673px">MY PAINTINGS</a>
    <a href="#" style="left:870px">CONTACT</a>
  </nav>

  <div class="portrait" role="img" aria-label="Portrait photo of the artist outdoors by the water"></div>

  <section class="about-copy">
    <h2 class="about-title">About Me</h2>
    <p>At vero eos et accusamus et iusto odio dignmos ducimus qui blanditiis praesentium voluptatum eniti atque corrupti quos dolores et quas molestturi sint occati cupiditate non provident, simue sunt in culpa qui officia deserunt mollitia animi, id est laborum et dolorum fuga. Et m quidem rerum facilis est et expedita distinctio. Nam libero tempore, cum soluta nobis est eligendi optio que nihil impedit quo minus id quod maxime placeat facere possimus, omnis voluptas assumenda est, omnis dolor repellendus.</p>
    <p>At vero eos et accusamus et iusto odio dignmos ducimus qui blanditiis praesentium voluptatum eniti atque corrupti quos dolores et quas molestturi sint occati cupiditate non provident, simue sunt in culpa qui officia deserunt mollitia animi, id est laborum et dolorum fuga. Et m quidem rerum facilis est et expedita distinctio.</p>
  </section>

  <footer class="site-footer">
    <div class="social-links">
      <a href="#">Nook</a>
      <a href="#">Wren</a>
      <a href="#">Lume</a>
    </div>
    <p class="copyright">©Copyright ©2022 Lorna Vessey Art. All Rights Reserved.</p>
  </footer>
</body>
</html>
```